Desktop and Networking Support Course 9.17.25

Important the ad should not be very busy with the text taking up the major part of the ad .. please do not make the text so big that it takes up most of the ad..
Flyer Design Brief for Graphic Artist
also i am looking for something unique or creative that it will stand out .
Size & Layout:
Full Page with Bleed: 8” x 10.75” + 0.25” bleed on all sides.
Footer Space: Leave a 1-inch margin at the bottom for footer content (e.g., contact info, logo, or call-to-action).
Target Audience:
College-age students (around 24 years old)
Located in the USA
Interested in creative, professional, and career-building opportunities
Purpose:
To attract students to enroll in a college program
Flyer should be eye-catching, unique, and creative
Text must be clear and readable,
Design Style:
Use vector art, typography, or photography — your choice
If using photography, feature a white young professional USA citizen:
Wearing a white collared shirt
not with long hair
Creative Direction:
The flyer should stand out visually — something people would want to look at and keep
Showcase creativity and professionalism
Use bold colors, dynamic layout, or unexpected design elements to grab attention
Avoid clutter — keep the design balanced and clean
Text Suggestions (can be adjusted):
Footer,
please leave one inch on the bottom for the footer

```html
<!DOCTYPE html>
<html lang="en">
<head>
<meta charset="utf-8">
<title>Desktop &amp; Network Support Course Flyer</title>
<link rel="stylesheet" href="https://fonts.googleapis.com/css2?family=Bebas+Neue&family=Poppins:wght@400;500;600&display=swap">
<style>
  :root {
    --page-bg: #bdbdbd;
    --navy-deep: #07172b;
    --navy: #0d223a;
    --teal: #1f5761;
    --ink: #0c1e33;
    --paper: #ffffff;
    --headline: #eef5fb;
    --photo-light: #d9dde2;
    --photo-mid: #8e98a4;
  }
  * { margin: 0; padding: 0; box-sizing: border-box; }
  html, body { width: 882px; height: 1200px; overflow: hidden; background: var(--page-bg); }
  .flyer {
    position: absolute; left: 94px; top: 91px; width: 676px; height: 1015px;
    overflow: hidden; color: var(--headline);
    background:
      radial-gradient(ellipse 420px 360px at 100% 0%, rgba(31,87,97,.75), transparent 70%),
      radial-gradient(ellipse 460px 260px at 100% 100%, rgba(31,87,97,.9), transparent 70%),
      linear-gradient(180deg, var(--navy) 0%, var(--navy-deep) 55%, var(--navy) 100%);
  }
  .display { font-family: "Bebas Neue", "Oswald", sans-serif; font-weight: 400; text-transform: uppercase; }
  .body-text { font-family: "Poppins", "Helvetica Neue", sans-serif; }

  .headline { position: absolute; left: 0; right: 0; top: 28px; text-align: center; font-size: 111px; line-height: 89px; letter-spacing: 0.5px; }
  .course-title { position: absolute; left: 22px; top: 236px; font-size: 70px; line-height: 67px; }
  .course-subtitle { position: absolute; left: 19px; top: 512px; font-size: 53px; line-height: 50px; }

  .benefits { position: absolute; left: 56px; list-style: none; font-size: 17px; font-weight: 500; }
  .benefits li { display: flex; align-items: center; gap: 18px; height: 20px; position: absolute; left: 0; white-space: nowrap; }
  .benefits svg { width: 22px; height: 22px; flex: none; }
  .benefits-skills { top: 388px; }
  .benefits-format { top: 634px; }

  .student-photo {
    position: absolute; left: 371px; top: 248px; width: 305px; height: 486px;
    background: radial-gradient(ellipse 140px 230px at 55% 60%, var(--photo-light) 0%, var(--photo-mid) 60%, transparent 100%);
    border-radius: 150px 150px 0 0; opacity: .9;
  }

  .stats-panel { position: absolute; left: 0; top: 734px; width: 676px; height: 187px; background: var(--paper); border-radius: 27px; color: var(--ink); }
  .stat-figure { position: absolute; left: 23px; top: 16px; font-size: 128px; line-height: 110px; letter-spacing: -1px; }
  .stat-label { position: absolute; left: 0; width: 216px; top: 120px; text-align: center; font-size: 17.5px; font-weight: 600; line-height: 26px; }
  .panel-divider { position: absolute; left: 222px; top: 22px; width: 1.5px; height: 148px; background: var(--ink); }
  .ranking { position: absolute; left: 246px; top: 65px; font-size: 35px; line-height: 29px; transform: scaleX(.93); transform-origin: left; white-space: nowrap; }

  .contact { position: absolute; top: 936px; left: 0; right: 0; height: 75px; }
  .contact-phone { position: absolute; left: 42px; top: 4px; font-size: 57px; line-height: 60px; transform: scaleX(.96); transform-origin: left; white-space: nowrap; }
  .contact-divider { position: absolute; left: 357px; top: 0; width: 1px; height: 72px; background: var(--headline); opacity: .8; }
  .contact-email { position: absolute; left: 396px; top: 20px; font-size: 31px; line-height: 32px; transform: scaleX(.92); transform-origin: left; white-space: nowrap; }
</style>
</head>
<body>
  <main class="flyer">
    <h1 class="headline display">Your Career Is<br>Just a Click Away</h1>

    <h2 class="course-title display">Desktop &amp; Network<br>Support Course</h2>

    <ul class="benefits benefits-skills body-text">
      <li style="top:0">
        <svg viewBox="0 0 22 22"><circle cx="10" cy="12" r="9.5" fill="#fff"/><path d="M5.5 12l3.5 3.5L19 4" fill="none" stroke="#0d223a" stroke-width="2.4" stroke-linecap="round" stroke-linejoin="round"/></svg>
        Hands-On Desktop &amp; Network Training</li>
      <li style="top:34px">
        <svg viewBox="0 0 22 22"><circle cx="10" cy="12" r="9.5" fill="#fff"/><path d="M5.5 12l3.5 3.5L19 4" fill="none" stroke="#0d223a" stroke-width="2.4" stroke-linecap="round" stroke-linejoin="round"/></svg>
        Real-World Troubleshooting Skills</li>
      <li style="top:73px">
        <svg viewBox="0 0 22 22"><circle cx="10" cy="12" r="9.5" fill="#fff"/><path d="M5.5 12l3.5 3.5L19 4" fill="none" stroke="#0d223a" stroke-width="2.4" stroke-linecap="round" stroke-linejoin="round"/></svg>
        Ready for IT Jobs</li>
    </ul>

    <h2 class="course-subtitle display">Master Desktop<br>Operating Systems</h2>

    <ul class="benefits benefits-format body-text">
      <li style="top:0">
        <svg viewBox="0 0 22 22"><circle cx="10" cy="12" r="9.5" fill="#fff"/><path d="M5.5 12l3.5 3.5L19 4" fill="none" stroke="#0d223a" stroke-width="2.4" stroke-linecap="round" stroke-linejoin="round"/></svg>
        In-Person and Remote Options</li>
      <li style="top:39px">
        <svg viewBox="0 0 22 22"><circle cx="10" cy="12" r="9.5" fill="#fff"/><path d="M5.5 12l3.5 3.5L19 4" fill="none" stroke="#0d223a" stroke-width="2.4" stroke-linecap="round" stroke-linejoin="round"/></svg>
        Partial Scholarships Offered</li>
    </ul>

    <div class="student-photo" role="img" aria-label="Photo of a smiling young professional with short hair in a white collared shirt, hands clasped"></div>

    <section class="stats-panel">
      <div class="stat-figure display">90%</div>
      <p class="stat-label body-text">Employment Rate<br>Class of 2024</p>
      <div class="panel-divider"></div>
      <p class="ranking display">Prepare for 3 of the Top 10 Tech Jobs<br>National Career Review 2025</p>
    </section>

    <footer class="contact">
      <div class="contact-phone display">(555) 214-7360</div>
      <div class="contact-divider"></div>
      <div class="contact-email display">info@nexalearning.com</div>
    </footer>
  </main>
</body>
</html>
```